Create modern and sleek business card for luxury real estate company

We're a "boutique" real estate office looking for a design that gets across a highly modern luxury brand. Blacks and whites are probably the best colors unless we try a silver foil for the logo. I've attached a version of our current logo here. I'd like to swap out the current font on there with Gotham Light Regular.

I'm looking to have one side of the card have the logo with the space for our agents info on the other side.

Target Market(s)

Young professionals in a "luxury" headspace

Industry/Entity Type

Real estate

Contact Information for Business Card

A place for agent name, cell number, website. The slogan "Quietly Redefining Home Living".

Font styles to use
Other font styles liked:
• Gotham Regular

Colors

Designer to choose only greyscale colors for use in the design.

Requirements
Must have
• Matte black as the background color. Clean lines and use of contrast. A specific design aspect that will use silver foil.
Nice to have
• Up in the air on integrating a QR code
Should not have
• Any houses or other real estate related design (ex: a clip art house)

```html
<!DOCTYPE html>
<html lang="en">
<head>
<meta charset="utf-8">
<title>Halvard Realty – Business Card</title>
<link rel="stylesheet" href="https://fonts.googleapis.com/css2?family=Montserrat:wght@300;400;700&family=Dancing+Script:wght@500&display=swap">
<style>
  :root {
    --backdrop: #2a2f36;
    --matte-black: #1b1a1b;
    --pattern-dark: #211f21;
    --pattern-light: #2c2a2d;
    --panel-top: #2e3033;
    --panel-bottom: #3b3e42;
    --silver: #c9c9cc;
    --silver-light: #eeeeef;
    --silver-dark: #8d8e92;
    --text-white: #f2f2f2;
    --text-soft: #d6d6d8;
  }
  * { margin: 0; padding: 0; box-sizing: border-box; }
  html, body {
    width: 1200px; height: 1200px; overflow: hidden;
    background: var(--backdrop);
  }
  .canvas {
    width: 1200px; height: 1200px;
    display: flex; align-items: center; justify-content: center;
  }
  .card {
    position: relative;
    width: 1000px; height: 540px;
    background: var(--matte-black);
    overflow: hidden;
    box-shadow: 0 24px 50px rgba(0,0,0,0.45);
  }
  .card__pattern {
    position: absolute; left: 0; top: 0;
    width: 100%; height: 250px;
    background: linear-gradient(100deg, var(--pattern-dark) 0%, var(--pattern-light) 55%, var(--pattern-dark) 100%);
  }
  .card__foil-rule {
    position: absolute; left: 0; top: 250px;
    width: 100%; height: 7px;
    background: linear-gradient(90deg, var(--silver-dark), var(--silver-light) 40%, var(--silver) 70%, var(--silver-dark));
  }
  .card__info-panel {
    position: absolute; left: 0; top: 257px;
    width: 100%; height: 283px;
    background: linear-gradient(160deg, var(--panel-bottom) 0%, var(--panel-top) 60%, #2a2b2d 100%);
  }
  .brand {
    position: absolute; left: 48px; top: 32px;
    display: flex; align-items: center; gap: 28px;
  }
  .brand__circle {
    width: 160px; height: 160px;
    border: 4px solid var(--silver);
    border-radius: 50%;
  }
  .brand__name {
    font-family: "Montserrat", sans-serif;
    font-weight: 300;
    font-size: 56px;
    line-height: 1.05;
    letter-spacing: 2px;
    color: var(--silver);
    text-transform: uppercase;
  }
  .slogan {
    position: absolute; left: 630px; top: 150px;
    font-family: "Dancing Script", cursive;
    font-weight: 500;
    font-size: 36px;
    line-height: 1.15;
    color: var(--silver);
    white-space: nowrap;
  }
  .slogan__second { display: block; padding-left: 18px; }
  .agent-name {
    position: absolute; left: 150px; top: 320px;
    font-family: "Montserrat", sans-serif;
    font-weight: 700;
    font-size: 40px;
    color: var(--text-white);
  }
  .contact {
    position: absolute; left: 560px; top: 308px;
    display: flex; gap: 18px;
  }
  .contact__icons { width: 40px; height: 160px; }
  .contact__list {
    list-style: none;
    font-family: "Montserrat", sans-serif;
    font-weight: 300;
    font-size: 26px;
    color: var(--text-soft);
    padding-top: 2px;
    white-space: nowrap;
  }
  .contact__list li { height: 52px; line-height: 40px; }
</style>
</head>
<body>
<main class="canvas">
  <article class="card">
    <div class="card__pattern" role="img" aria-label="Subtle geometric cube line pattern on matte black"></div>
    <div class="card__foil-rule"></div>
    <div class="card__info-panel"></div>

    <div class="brand">
      <div class="brand__circle"></div>
      <div class="brand__name">Halvard<br>Realty</div>
    </div>

    <p class="slogan">“Quietly Redefining<span class="slogan__second">Home Living”</span></p>

    <h1 class="agent-name">Lorem ipsum</h1>

    <div class="contact">
      <svg class="contact__icons" viewBox="0 0 40 160" aria-hidden="true">
        <g fill="none" stroke="#e6e6e8" stroke-width="2.5">
          <line x1="20" y1="38" x2="20" y2="62"/>
          <line x1="20" y1="90" x2="20" y2="114"/>
          <circle cx="20" cy="20" r="17"/>
          <circle cx="20" cy="76" r="17"/>
          <circle cx="20" cy="130" r="17"/>
          <path d="M14 13c1-1 2.5-1 3 0l1.5 3c.4.9 0 1.6-.8 2.2 1 2 2.4 3.4 4.4 4.4.6-.8 1.3-1.2 2.2-.8l3 1.5c1 .5 1 2 0 3-3 3-14-8-13.3-13.3z" fill="#e6e6e8" stroke="none"/>
          <rect x="11" y="70" width="18" height="12" stroke-width="2"/>
          <path d="M11 70l9 7 9-7" stroke-width="2"/>
        </g>
        <path d="M20 121l6 12-6-3-6 3z" fill="#e6e6e8"/>
      </svg>
      <ul class="contact__list">
        <li>555.018.4420</li>
        <li>agent@halvardrealty.com</li>
        <li>www.halvardrealty.com</li>
      </ul>
    </div>
  </article>
</main>
</body>
</html>
```